Brightmill Data Works

Our company is about IT hardwares and IT solutions. IT hardware such as PC, RAMS, storage and servers. IT solutions such as project management, BA. We are also selling new technology too.

Target Market(s)

Consumer, Small to Medium Business, Corporate

Requirements
Must have
• The business card must have the following:
• Name:
• Title:
• Contact Number:
• Email address:
• Website:
• Color: Must match the logo color upgrade

```html
<!DOCTYPE html>
<html lang="en">
<head>
<meta charset="utf-8">
<title>Brightmill Data Works — Business Card</title>
<link href="https://fonts.googleapis.com/css2?family=Lato:wght@400;700&display=swap" rel="stylesheet">
<style>
  :root {
    --stage: #151515;
    --card: #232323;
    --card-back: #1c1c1c;
    --pattern: #191919;
    --accent: #e0912b;
    --text: #f2f2f2;
    --muted: #d8d8d8;
  }
  * { margin: 0; padding: 0; box-sizing: border-box; }
  html, body { width: 1200px; height: 912px; overflow: hidden; background: var(--stage); }
  body { position: relative; font-family: "Lato", sans-serif; }

  .card {
    position: absolute;
    width: 560px;
    height: 320px;
    border-radius: 2px;
    box-shadow: 0 18px 40px rgba(0,0,0,0.55);
    overflow: hidden;
  }

  /* Back side */
  .card-back { left: 60px; top: 100px; background: var(--card-back); }
  .back-pattern {
    position: absolute; inset: 0;
    background: linear-gradient(135deg, var(--pattern), #202020 60%, var(--pattern));
  }
  .back-name {
    position: absolute; right: 40px; top: 36px;
    display: flex; align-items: center; gap: 8px;
    color: var(--accent); font-weight: 700; font-size: 15px; letter-spacing: 0.5px;
  }

  /* Front side */
  .card-front { left: 580px; top: 492px; background: var(--card); }
  .brand {
    position: absolute; left: 36px; top: 140px; width: 230px;
    display: flex; align-items: center; gap: 10px;
  }
  .brand-square { width: 14px; height: 14px; background: var(--accent); flex: none; }
  .brand-name { color: var(--text); font-weight: 700; font-size: 21px; letter-spacing: 0.3px; line-height: 1.2; }

  .divider {
    position: absolute; left: 290px; top: 60px;
    width: 1.5px; height: 200px; background: var(--accent);
  }

  .contact { position: absolute; left: 318px; top: 62px; color: var(--muted); }
  .person-name { color: var(--accent); font-weight: 700; font-size: 22px; line-height: 1.1; }
  .person-title { font-size: 13px; margin-top: 3px; }
  .address { font-size: 13px; line-height: 1.4; margin-top: 14px; }
  .lines { list-style: none; margin-top: 12px; }
  .lines li { display: flex; align-items: center; gap: 9px; font-size: 13px; line-height: 1.55; }
  .lines svg { width: 12px; height: 12px; fill: var(--accent); flex: none; }
</style>
</head>
<body>

  <section class="card card-back" aria-label="Business card back">
    <div class="back-pattern" role="img" aria-label="Tonal repeating brand pattern across the card back"></div>
    <div class="back-name"><span class="brand-square" style="width:10px;height:10px;background:var(--accent)"></span>Brightmill Data Works</div>
  </section>

  <section class="card card-front" aria-label="Business card front">
    <div class="brand">
      <span class="brand-square"></span>
      <span class="brand-name">Brightmill Data Works</span>
    </div>

    <div class="divider"></div>

    <div class="contact">
      <p class="person-name">Daniel Archer</p>
      <p class="person-title">Manager</p>
      <p class="address">418 Cedar Row Lane<br>Austin, TX 78702</p>
      <ul class="lines">
        <li>
          <svg viewBox="0 0 24 24" aria-hidden="true"><path d="M6.6 10.8a15.1 15.1 0 0 0 6.6 6.6l2.2-2.2c.3-.3.7-.4 1-.2 1.1.4 2.3.6 3.6.6.6 0 1 .4 1 1V20c0 .6-.4 1-1 1C10.6 21 3 13.4 3 4c0-.6.4-1 1-1h3.5c.6 0 1 .4 1 1 0 1.3.2 2.5.6 3.6.1.3 0 .7-.2 1z"/></svg>
          555 014 2280
        </li>
        <li>
          <svg viewBox="0 0 24 24" aria-hidden="true"><path d="M6 2h12v5H6zM3 8h18a1 1 0 0 1 1 1v8h-4v5H6v-5H2V9a1 1 0 0 1 1-1zm5 7v5h8v-5z"/></svg>
          555 014 2281
        </li>
        <li>
          <svg viewBox="0 0 24 24" aria-hidden="true"><path d="M2 5h20v14H2zm2 2v.5l8 5 8-5V7l-8 5z"/></svg>
          info@brightmilldata.com
        </li>
        <li>
          <svg viewBox="0 0 24 24" aria-hidden="true"><path d="M12 2a10 10 0 1 0 0 20 10 10 0 0 0 0-20zm6.9 9h-3a15 15 0 0 0-1.2-5.5A8 8 0 0 1 18.9 11zM12 4.1c.9 1.3 1.7 3.7 1.9 6.9h-3.8c.2-3.2 1-5.6 1.9-6.9zM9.3 5.5A15 15 0 0 0 8.1 11h-3a8 8 0 0 1 4.2-5.5zM5.1 13h3a15 15 0 0 0 1.2 5.5A8 8 0 0 1 5.1 13zm6.9 6.9c-.9-1.3-1.7-3.7-1.9-6.9h3.8c-.2 3.2-1 5.6-1.9 6.9zm2.7-1.4a15 15 0 0 0 1.2-5.5h3a8 8 0 0 1-4.2 5.5z"/></svg>
          www.brightmilldata.com
        </li>
      </ul>
    </div>
  </section>

</body>
</html>
```